Design a compelling Tarnwove Business Card that will drive people to my site

I want a business card that I can give to people—less to tell them who I am and more to direct them to my website. My website is a portal for Pelmor Aquatics Officials and a place for people who want to become Pelmor Aquatics Officials.
I am uploading my official company logo as well as a business card mockup that I did on my own. Please feel free to completely stray from this design.
I've included a screen recording of the homepage of my website as well.
Target Market(s)
Pelmor Aquatics Officials and people who desire to become one
Contact Information for Business Card
website url
Look and feel
Each slider illustrates characteristics of the customer's brand and the style your logo design should communicate.

```html
<!DOCTYPE html>
<html lang="en">
<head>
<meta charset="utf-8">
<title>Tarnwove Business Card</title>
<link href="https://fonts.googleapis.com/css2?family=Poppins:wght@400;500;600;700&display=swap" rel="stylesheet">
<style>
  :root {
    --page: #e6e7eb;
    --card-blue: #3a52a6;
    --card-blue-deep: #344a98;
    --accent-light: #8fa3dc;
    --faint-mark: #4a62b3;
    --white: #ffffff;
  }
  * { box-sizing: border-box; margin: 0; padding: 0; }
  html, body {
    width: 1186px; height: 1200px; overflow: hidden;
    background: var(--page);
    font-family: "Poppins", sans-serif;
  }
  .canvas { position: relative; width: 1186px; height: 1200px; }
  .card {
    position: absolute; left: 153px; width: 880px; height: 502px;
    background: var(--card-blue); overflow: hidden;
    box-shadow: 0 10px 28px rgba(20, 30, 70, 0.22);
  }
  .card--front { top: 60px; }
  .card--back { top: 638px; }

  /* front */
  .brand-mark-space {
    position: absolute; left: 130px; top: 58px; width: 280px; height: 80px;
    display: flex; align-items: center; justify-content: center;
  }
  .brand-dot {
    width: 30px; height: 30px; border-radius: 50%;
    background: var(--accent-light); flex: none;
  }
  .brand-name {
    position: absolute; left: 54px; top: 150px;
    font-size: 80px; font-weight: 600; color: var(--white);
    letter-spacing: -1px; line-height: 1;
  }
  .holder {
    position: absolute; right: 58px; top: 62px; text-align: right;
  }
  .holder__name {
    font-size: 30px; font-weight: 700; color: var(--accent-light); line-height: 1.2;
  }
  .holder__role {
    font-size: 23px; font-weight: 400; color: var(--white); line-height: 1.3;
  }
  .edge-tab {
    position: absolute; right: -10px; top: 62px; width: 28px; height: 74px;
    background: var(--white); border-radius: 10px;
  }
  .backdrop-mark {
    position: absolute; left: 340px; top: 300px; width: 540px; height: 180px;
    background: radial-gradient(ellipse at 50% 55%, var(--faint-mark) 0%, rgba(74,98,179,0) 70%);
  }
  .contact {
    position: absolute; left: 56px; top: 350px; list-style: none;
    color: var(--white); font-size: 25px; line-height: 33px;
  }
  .contact li { display: flex; align-items: center; gap: 6px; }
  .contact svg { width: 18px; height: 18px; flex: none; }
  .base-band {
    position: absolute; left: 0; right: 0; bottom: 0; height: 18px; display: flex; gap: 8px;
  }
  .base-band__white { flex: 1; background: var(--white); }
  .base-band__light { flex: 1; background: var(--accent-light); }

  /* back */
  .pattern-field {
    position: absolute; inset: 0;
    background: linear-gradient(160deg, var(--card-blue) 0%, var(--card-blue-deep) 100%);
  }
  .back-name {
    position: absolute; left: 297px; top: 212px;
    font-size: 60px; font-weight: 600; color: var(--white); line-height: 1;
    letter-spacing: -0.5px;
  }
  .back-mark {
    position: absolute; left: 190px; top: 360px;
    width: 24px; height: 24px; border-radius: 50%; background: var(--accent-light);
  }
  .back-tagline {
    position: absolute; left: 293px; top: 352px;
    font-size: 27px; font-weight: 500; color: var(--white); white-space: nowrap; line-height: 1.4;
  }
</style>
</head>
<body>
<main class="canvas">

  <section class="card card--front" aria-label="Business card front">
    <div class="backdrop-mark" role="img" aria-label="Faint brand decoration"></div>

    <div class="brand-mark-space"><span class="brand-dot"></span></div>
    <p class="brand-name">Tarnwove</p>

    <div class="holder">
      <p class="holder__name">Marcus Hallbrook</p>
      <p class="holder__role">CEO &amp; Founder</p>
    </div>
    <div class="edge-tab"></div>

    <ul class="contact">
      <li>
        <svg viewBox="0 0 20 20" aria-hidden="true"><path fill="#fff" d="M4 3h4l1.5 4-2 1.5a10 10 0 0 0 4 4L13 10.5l4 1.5v4a2 2 0 0 1-2 2A14 14 0 0 1 2 5a2 2 0 0 1 2-2z"/></svg>
        (555) 210-4837
      </li>
      <li>
        <svg viewBox="0 0 20 20" aria-hidden="true"><rect x="2" y="4" width="16" height="12" rx="2" fill="#fff"/><path d="M3 5l7 6 7-6" stroke="#3a52a6" stroke-width="1.6" fill="none"/></svg>
        marcus@tarnwove.com
      </li>
      <li>
        <svg viewBox="0 0 20 20" aria-hidden="true"><circle cx="10" cy="10" r="8" fill="#fff"/><path d="M2 10h16M10 2c3 3 3 13 0 16M10 2c-3 3-3 13 0 16" stroke="#3a52a6" stroke-width="1.3" fill="none"/></svg>
        www.tarnwove.com
      </li>
    </ul>

    <div class="base-band">
      <span class="base-band__white"></span>
      <span class="base-band__light"></span>
    </div>
  </section>

  <section class="card card--back" aria-label="Business card back">
    <div class="pattern-field" role="img" aria-label="Embossed repeating brand pattern in deep blue"></div>
    <p class="back-name">Tarnwove</p>
    <span class="back-mark"></span>
    <p class="back-tagline">The Poolside Referee’s Gateway</p>
  </section>

</main>
</body>
</html>
```